WEBSITE DESIGN, VELTRA paint and panel

We are in need of a website for Veltra Paint & Panel based in Brisbane, Australia. We are a boutique Automotive Paint & Panel Company that provides services to all makes and models of vehicles. We have attached a logo that is still in draft stage but gives you an idea of the colour scheme and fonts and overall impact we are looking for. We are after a white background so this is clean and crisp whilst being sleek, modern and professional. The website must represent our slogan of Glowing finish on the Gleaming frame. The website must therefore be visually effective as our product is to get colour and placement on vehicle body's correct so the website must have this impact on our clients. We are after a widescreen webpage that is simple and logical to navigate. The final design should give clients the confidence that we can deliver on our promise.
Updates

Target Market(s)

Vehicle Owners who have a need for panel repairs and people who want to reinvigorate their car with a new coat of paint.

Industry/Entity Type

Car Repair

Coding

Coded - Design and coding required

Number of Pages Required

5+ page

Font styles to use
Sans Serif

Colors
ffffff
ffc214
000000

Requirements
Must have
• Page 1 - Home Page
• Page 2 - Our Process
• Page 3 - Private Customers
• Page 4 - Fleet & Corporate
• Page 5 - Insurance
• Page 6 - Get a Quote
• Page 7 - Connect (Contacts Page)
• Same font and colour scheme as the logo.
Should not have
• A typical mechanical/paint and panel layout which looks like a template website.

```html
<!DOCTYPE html>
<html lang="en">
<head>
<meta charset="utf-8">
<title>Veltra Paint &amp; Panel</title>
<link href="https://fonts.googleapis.com/css2?family=Roboto:wght@400;500;700&family=Roboto+Condensed:wght@400;700&display=swap" rel="stylesheet">
<style>
:root{
  --red:#c4161c;
  --red-dark:#9e1015;
  --ink:#222;
  --text:#666;
  --muted:#999;
  --dark:#1f1f1f;
  --darker:#161616;
  --band:#ececec;
  --line:#dcdcdc;
  --white:#fff;
  --gold:#ffc214;
}
*{box-sizing:border-box;margin:0;padding:0}
html,body{width:800px;height:1200px;overflow:hidden;background:var(--white)}
body{font-family:"Roboto",Arial,sans-serif;color:var(--text);font-size:9px;line-height:1.5;position:relative}
.abs{position:absolute}

/* header */
.topbar{left:0;top:0;width:800px;height:48px;background:var(--dark)}
.brand{left:60px;top:10px;display:flex;align-items:center;gap:6px;color:var(--white);font-family:"Roboto Condensed",sans-serif;font-weight:700;font-size:17px;letter-spacing:1px}
.brand-dot{width:10px;height:10px;border-radius:50%;background:var(--red)}
.top-contact{right:60px;top:15px;display:flex;gap:18px;color:#ccc;font-size:9px}
.top-contact span{display:flex;align-items:center;gap:5px}
.nav{left:53px;top:48px;width:694px;height:32px;background:var(--red);display:flex;align-items:center;padding:0 12px;gap:0}
.nav a{color:var(--white);text-decoration:none;font-family:"Roboto Condensed",sans-serif;font-weight:700;font-size:10px;padding:0 13px;line-height:32px;height:32px}
.nav a.active{background:var(--red-dark)}

/* hero */
.hero{left:53px;top:80px;width:694px;height:315px;background:linear-gradient(110deg,#1d2c6e 0%,#2f47a8 30%,#6d7d9a 55%,#c9c2b6 75%,#8a8f96 100%)}
.hero-title{left:53px;top:170px;width:694px;text-align:center;color:var(--white);font-weight:700;font-size:46px;line-height:1.1;text-shadow:0 2px 6px rgba(0,0,0,.45)}
.hero-dots{left:0;width:800px;top:368px;display:flex;justify-content:center;gap:6px}
.hero-dots i{width:7px;height:7px;border-radius:50%;background:rgba(255,255,255,.55)}
.hero-dots i.on{background:var(--white)}

/* welcome */
.welcome{left:80px;top:410px;width:640px;text-align:center}
.section-title{font-family:"Roboto Condensed",sans-serif;font-weight:700;color:var(--ink);font-size:15px;letter-spacing:.3px}
.welcome p{margin:8px 0 10px}
.btn{display:inline-block;background:var(--red);color:var(--white);font-family:"Roboto Condensed",sans-serif;font-weight:700;font-size:9px;padding:6px 13px;text-decoration:none}

/* services band */
.band{left:0;top:575px;width:800px;height:210px;background:var(--band)}
.services{left:53px;top:592px;width:190px}
.services .section-title{color:#444}
.services p{margin:8px 0 14px}
.video{left:268px;top:600px;width:222px;height:133px;background:linear-gradient(120deg,#3a3a3a,#7a1e22 60%,#b9b2aa)}
.play{left:364px;top:652px}

/* quote */
.quote{left:513px;top:566px;width:236px;height:290px;background:var(--dark);padding:0 16px}
.quote-head{height:34px;line-height:34px;text-align:center;color:var(--white);font-family:"Roboto Condensed",sans-serif;font-weight:700;font-size:15px;letter-spacing:.5px;margin:0 -16px;position:relative}
.quote-head:after{content:"";position:absolute;left:50%;bottom:-6px;margin-left:-6px;border:6px solid transparent;border-bottom:0;border-top-color:var(--dark)}
.quote form{background:var(--red);margin:6px -6px 0;padding:10px;height:240px}
.field{background:var(--white);height:20px;margin-bottom:7px;font-size:8px;color:var(--muted);padding:4px 7px}
.field.msg{height:66px}
.quote .send{float:right;background:var(--darker);color:var(--white);border:0;font-family:"Roboto Condensed",sans-serif;font-weight:700;font-size:9px;padding:6px 11px;margin-top:2px}

/* cards */
.card{top:795px;width:205px;height:258px;border:1px solid var(--line);padding:11px}
.card-1{left:53px}
.card-2{left:270px}
.card .section-title{font-size:13px;line-height:1.15;height:32px}
.card-img{height:92px;margin:4px 0 10px}
.card-1 .card-img{background:linear-gradient(120deg,#c8c0b8,#b92a34 45%,#2d4b9a 80%)}
.card-2 .card-img{background:linear-gradient(120deg,#555,#9aa0a8 50%,#2a2a2a)}
.card p{margin-bottom:12px}

.private{left:513px;top:860px;width:234px;height:193px;border:1px solid var(--line);padding:14px}
.private .section-title{font-size:13px;margin-bottom:12px}
.person{display:flex;gap:10px;margin-bottom:14px}
.avatar{width:36px;height:36px;flex:none;border-radius:50%;background:linear-gradient(135deg,#d9c6b8,#7e6a5e)}
.person h4{color:var(--red);font-family:"Roboto Condensed",sans-serif;font-size:11px}

/* footer */
.footer{left:0;top:1062px;width:800px;height:138px;background:var(--dark);color:#aaa;font-size:8px}
.f-col{top:14px}
.f-col h5{color:var(--white);font-family:"Roboto Condensed",sans-serif;font-size:10px;margin-bottom:6px}
.f-col ul{list-style:none}
.f-brand{left:60px;top:16px}
.f-copy{left:60px;top:70px;line-height:1.4}
.f-links{left:225px}
.f-links2{left:345px;top:33px}
.f-contact{left:470px}
.f-contact li{display:flex;gap:5px;align-items:center;margin-bottom:3px}
.f-social{left:647px}
.social{display:flex;gap:6px}
.social i{width:14px;height:14px;background:#bbb;border-radius:2px}
</style>
</head>
<body>

<header>
  <div class="abs topbar"></div>
  <div class="abs brand"><span class="brand-dot"></span>Veltra</div>
  <div class="abs top-contact">
    <span><svg width="9" height="9" viewBox="0 0 24 24"><path fill="#ccc" d="M6.6 10.8a15 15 0 006.6 6.6l2.2-2.2c.3-.3.7-.4 1-.2 1.1.4 2.3.6 3.6.6.6 0 1 .4 1 1V20c0 .6-.4 1-1 1C10.6 21 3 13.4 3 4c0-.6.4-1 1-1h3.5c.6 0 1 .4 1 1 0 1.3.2 2.5.6 3.6.1.3 0 .7-.2 1z"/></svg>(07) 3100 4455</span>
    <span><svg width="10" height="8" viewBox="0 0 20 16"><rect x="1" y="1" width="18" height="14" fill="none" stroke="#ccc" stroke-width="2"/><path d="M1 1l9 7 9-7" fill="none" stroke="#ccc" stroke-width="2"/></svg>hello@veltrapanel.com.au</span>
  </div>
  <nav class="abs nav">
    <a class="active">HOME</a><a>OUR PROCESS</a><a>PRIVATE CUSTOMERS</a><a>FLEET &amp; CORPORATE INSURANCE</a><a>GET A QUOTE</a><a>CONNECT</a>
  </nav>
</header>

<section>
  <div class="abs hero" role="img" aria-label="Painter spraying a blue car body in a paint booth"></div>
  <h1 class="abs hero-title">Glowing finish on the<br>Gleaming frame</h1>
  <div class="abs hero-dots"><i class="on"></i><i></i><i></i><i></i></div>
</section>

<section class="abs welcome">
  <h2 class="section-title">WELCOME TO OUR WEBSITE</h2>
  <p>Every vehicle that rolls into our Brisbane workshop is treated with care. We match colour by eye and by spectrometer, repair panels to factory lines and finish each job with a deep, even gloss that lasts. From small dents to full resprays, our team delivers work you can trust.</p>
  <a class="btn">READ MORE</a>
</section>

<div class="abs band"></div>
<section class="abs services">
  <h2 class="section-title">OUR SERVICES</h2>
  <p>We repair dents, scratches and collision damage, then refinish panels with premium paint systems. Watch how our team brings a tired car back to showroom condition.</p>
  <a class="btn">READ MORE</a>
</section>
<div class="abs video" role="img" aria-label="Video still of a technician in the paint workshop"></div>
<svg class="abs play" width="30" height="30" viewBox="0 0 30 30"><circle cx="15" cy="15" r="14" fill="#fff"/><path d="M12 9l9 6-9 6z" fill="#333"/></svg>

<aside class="abs quote">
  <div class="quote-head">GET A QUOTE</div>
  <form>
    <div class="field">Your Name</div>
    <div class="field">Email Address</div>
    <div class="field">Phone No</div>
    <div class="field">Subject</div>
    <div class="field msg">Message</div>
    <button class="send" type="button">GET QUOTE</button>
  </form>
</aside>

<article class="abs card card-1">
  <h3 class="section-title">OUR PROCESS</h3>
  <div class="card-img" role="img" aria-label="Paint colour swatches fanned out"></div>
  <p>From first quote to final polish, each step is checked and signed off.</p>
  <a class="btn">READ MORE</a>
</article>
<article class="abs card card-2">
  <h3 class="section-title">FLEET &amp; CORPORATE INSURANCE</h3>
  <div class="card-img" role="img" aria-label="Row of fleet cars parked in a lot"></div>
  <p>Priority repairs that keep your fleet on the road and claims simple.</p>
  <a class="btn">READ MORE</a>
</article>
<article class="abs private">
  <h3 class="section-title">PRIVATE CUSTOMERS</h3>
  <div class="person"><div class="avatar" role="img" aria-label="Customer portrait"></div><div><h4>Name Heading</h4><p>Friendly service and honest quotes for your car.</p></div></div>
  <div class="person"><div class="avatar" role="img" aria-label="Customer portrait"></div><div><h4>Name Heading</h4><p>Friendly service and honest quotes for your car.</p></div></div>
</article>

<footer>
  <div class="abs footer">
    <div class="abs brand f-brand" style="top:16px"><span class="brand-dot"></span>Veltra</div>
    <div class="abs f-copy">Copyright &copy; 2015, Veltra<br>All Rights Reserved</div>
    <div class="abs f-col f-links"><h5>COMPANY</h5><ul><li>Home</li><li>Our Process</li><li>Private Customers</li><li>Fleet &amp; Corporate Insurance</li></ul></div>
    <div class="abs f-col f-links2"><ul><li>Get a Quote</li><li>Connect</li></ul></div>
    <div class="abs f-col f-contact"><h5>CONTACT INFO</h5><ul>
      <li><svg width="8" height="10" viewBox="0 0 16 20"><path fill="#aaa" d="M8 0a7 7 0 00-7 7c0 5 7 13 7 13s7-8 7-13a7 7 0 00-7-7zm0 10a3 3 0 110-6 3 3 0 010 6z"/></svg>12 Shed Lane, Brisbane QLD 4000</li>
      <li><svg width="8" height="8" viewBox="0 0 24 24"><path fill="#aaa" d="M6.6 10.8a15 15 0 006.6 6.6l2.2-2.2c.3-.3.7-.4 1-.2 1.1.4 2.3.6 3.6.6.6 0 1 .4 1 1V20c0 .6-.4 1-1 1C10.6 21 3 13.4 3 4c0-.6.4-1 1-1h3.5c.6 0 1 .4 1 1 0 1.3.2 2.5.6 3.6.1.3 0 .7-.2 1z"/></svg>(07) 3100 4455</li>
      <li><svg width="9" height="7" viewBox="0 0 20 16"><rect x="1" y="1" width="18" height="14" fill="none" stroke="#aaa" stroke-width="2"/><path d="M1 1l9 7 9-7" fill="none" stroke="#aaa" stroke-width="2"/></svg>hello@veltrapanel.com.au</li>
    </ul></div>
    <div class="abs f-col f-social"><h5>CONNECT US</h5><div class="social"><i></i><i></i><i></i></div></div>
  </div>
</footer>

</body>
</html>
```